Business Card Design for Training Business

Clear Path Coaching is a new business that delivers training and other services with a focus on topics related to mental health and wellbeing, for example, Wellmind Response Course, Resilience etc. We have a strong focus on evidence-based psychology and neuroscience. I have a logo which I will upload with the brief, so please consider colours that work well with the logo.
Target Market(s)
Adults, workplaces (particularly government and not-for-profits)
Industry/Entity Type
Business
Contact Information for Business Card
Head Strong TrainingSamantha SellwoodDirector0438 770 850sam@headstrongtraining.com.auwww.headstrongtraining.com.au

```html
<!DOCTYPE html>
<html lang="en">
<head>
<meta charset="utf-8">
<title>Clear Path Coaching – Business Card</title>
<link rel="stylesheet" href="https://fonts.googleapis.com/css2?family=Lato:wght@300;400;700&display=swap">
<style>
  :root {
    --page-bg: #ebe7e3;
    --card-white: #ffffff;
    --band-brown: #6d6461;
    --accent-teal: #2fc4c8;
    --text-brown: #7b716d;
    --text-grey: #8a8380;
    --rule-grey: #b9b3b0;
  }
  * { margin: 0; padding: 0; box-sizing: border-box; }
  html, body {
    width: 1200px;
    height: 1022px;
    overflow: hidden;
    background: var(--page-bg);
    font-family: "Lato", Arial, sans-serif;
  }
  .business-card {
    position: absolute;
    left: 150px;
    top: 254px;
    width: 900px;
    height: 514px;
    background: var(--card-white);
    border-radius: 6px;
    overflow: hidden;
    box-shadow: 0 10px 30px rgba(60, 50, 45, 0.18);
  }
  .card-bands {
    position: absolute;
    inset: 0;
    width: 100%;
    height: 100%;
  }
  .brand-block {
    position: absolute;
    left: 70px;
    top: 205px;
    display: flex;
    align-items: center;
    gap: 20px;
  }
  .brand-mark {
    width: 84px;
    height: 84px;
    border: 2px solid var(--accent-teal);
    border-radius: 50%;
    flex: none;
  }
  .brand-name {
    font-weight: 300;
    color: var(--text-grey);
    line-height: 1.1;
  }
  .brand-name .brand-main {
    display: block;
    font-size: 34px;
    letter-spacing: 2px;
    text-transform: uppercase;
  }
  .brand-name .brand-sub {
    display: block;
    font-size: 15px;
    letter-spacing: 8px;
    text-transform: uppercase;
    text-align: center;
    margin-top: 4px;
  }
  .divider {
    position: absolute;
    left: 455px;
    top: 150px;
    width: 1px;
    height: 220px;
    background: var(--rule-grey);
  }
  .contact-block {
    position: absolute;
    left: 485px;
    top: 172px;
    color: var(--text-brown);
  }
  .person-name {
    font-size: 34px;
    font-weight: 700;
    letter-spacing: 0.3px;
  }
  .person-role {
    font-size: 18px;
    color: var(--accent-teal);
    margin: 2px 0 18px;
  }
  .contact-list {
    list-style: none;
    font-size: 18px;
    color: var(--text-grey);
  }
  .contact-list li {
    display: flex;
    align-items: center;
    gap: 10px;
    line-height: 1.55;
  }
  .contact-icon {
    width: 15px;
    height: 15px;
    flex: none;
    fill: none;
    stroke: var(--accent-teal);
    stroke-width: 1.8;
  }
</style>
</head>
<body>
  <div class="business-card">
    <svg class="card-bands" viewBox="0 0 900 514" aria-hidden="true">
      <path d="M0,0 H900 V96 C620,34 280,18 0,34 Z" fill="var(--band-brown)"/>
      <path d="M0,38 C280,22 620,38 900,100" fill="none" stroke="var(--accent-teal)" stroke-width="4"/>
      <path d="M0,514 V414 C270,484 600,500 900,482 V514 Z" fill="var(--band-brown)"/>
      <path d="M0,410 C270,480 600,496 900,478" fill="none" stroke="var(--accent-teal)" stroke-width="4"/>
    </svg>

    <div class="brand-block">
      <span class="brand-mark"></span>
      <p class="brand-name">
        <span class="brand-main">Clear Path</span>
        <span class="brand-sub">Coaching</span>
      </p>
    </div>

    <div class="divider"></div>

    <div class="contact-block">
      <h1 class="person-name">Rebecca Tanfield</h1>
      <p class="person-role">Director</p>
      <ul class="contact-list">
        <li>
          <svg class="contact-icon" viewBox="0 0 16 16"><path d="M4 1.5 L6.5 4.5 L5 6.5 C6 8.5 7.5 10 9.5 11 L11.5 9.5 L14.5 12 L13 14.5 C7 14 2 9 1.5 3 Z"/></svg>
          <span>0491 362 517</span>
        </li>
        <li>
          <svg class="contact-icon" viewBox="0 0 16 16"><rect x="1.5" y="3.5" width="13" height="9" rx="1"/><path d="M1.5 4 L8 9 L14.5 4"/></svg>
          <span>bec@clearpathcoaching.example.au</span>
        </li>
        <li>
          <svg class="contact-icon" viewBox="0 0 16 16"><circle cx="8" cy="8" r="6.5"/><ellipse cx="8" cy="8" rx="2.8" ry="6.5"/><path d="M1.5 8 H14.5"/></svg>
          <span>www.clearpathcoaching.example.au</span>
        </li>
      </ul>
    </div>
  </div>
</body>
</html>
```